Business Cards - Brightpath Horizon

need to design unique business card for my mortgage business. I need to design credit card style business card for my business or any unique idea that you might have

Target Market(s)

Home Loan customers

Industry/Entity Type

Mortgage Brokerage

Contact Information for Business Card

please design credit card style or very unique style business card

Colors

Designer to choose colors to be used in the design.

Requirements
Must have
• Name
• position
• Phone number
• fax number
• email address
• website address
• social media address
• All above fields will be provided once design in finalised

```html
<!DOCTYPE html>
<html lang="en">
<head>
<meta charset="utf-8">
<title>Brightpath Horizon – Business Cards</title>
<link rel="stylesheet" href="https://fonts.googleapis.com/css2?family=Work+Sans:wght@400;500&display=swap">
<style>
  :root {
    --canvas-bg: #ececec;
    --card-white: #ffffff;
    --brand-orange: #f48a20;
    --brand-navy: #2e44a0;
    --accent-sky: #1ca3e0;
    --text-dark: #333333;
    --text-grey: #555555;
  }
  * { box-sizing: border-box; margin: 0; padding: 0; }
  html, body {
    width: 1200px; height: 1000px; overflow: hidden;
    background: var(--canvas-bg);
    font-family: "Work Sans", Arial, sans-serif;
  }
  .stage { position: relative; width: 1200px; height: 1000px; }

  .card {
    position: absolute; left: 255px; width: 666px;
    border-radius: 22px; overflow: hidden;
    box-shadow: 0 6px 16px rgba(0,0,0,0.18);
  }

  /* Front */
  .card--front { top: 100px; height: 380px; background: var(--card-white); }
  .brand-lockup {
    position: absolute; left: 70px; top: 0; width: 250px; height: 380px;
    display: flex; align-items: center; justify-content: center; gap: 10px;
  }
  .brand-lockup__dot {
    width: 14px; height: 14px; border-radius: 50%; background: var(--brand-orange); flex: none;
  }
  .brand-lockup__name {
    font-weight: 500; font-size: 30px; line-height: 1.1;
    color: var(--brand-navy); text-align: left;
  }
  .divider {
    position: absolute; left: 342px; top: 100px; width: 2px; height: 180px;
    background: var(--accent-sky);
  }
  .contact { position: absolute; left: 380px; top: 96px; }
  .contact__name {
    font-size: 25px; font-weight: 400; letter-spacing: 1.5px;
    color: var(--accent-sky); text-transform: uppercase;
  }
  .contact__role { font-size: 15px; color: var(--text-dark); margin-top: 6px; font-weight: 500; }
  .contact__address { font-size: 15px; color: var(--text-grey); margin-top: 22px; line-height: 20px; }
  .contact__list { list-style: none; margin-top: 20px; }
  .contact__list li {
    display: flex; align-items: center; gap: 9px;
    font-size: 15px; color: var(--text-grey); line-height: 19px;
  }
  .contact__list svg { width: 10px; height: 10px; flex: none; }

  .front-bands { position: absolute; left: 0; bottom: 0; width: 666px; height: 32px; }

  /* Back */
  .card--back {
    top: 520px; height: 378px; background: var(--brand-orange);
    display: flex; flex-direction: column; align-items: center;
  }
  .card--back .brand-lockup {
    position: static; width: auto; height: auto; margin-top: 160px;
  }
  .card--back .brand-lockup__dot { background: var(--card-white); width: 18px; height: 18px; }
  .card--back .brand-lockup__name { color: var(--card-white); font-size: 40px; }
  .back-web {
    position: absolute; bottom: 26px; left: 0; right: 0; text-align: center;
    color: var(--card-white); font-size: 15px; letter-spacing: 1.3px;
  }
</style>
</head>
<body>
<main class="stage">
  <section class="card card--front" aria-label="Business card front">
    <div class="brand-lockup">
      <span class="brand-lockup__dot"></span>
      <span class="brand-lockup__name">Brightpath<br>Horizon</span>
    </div>
    <div class="divider"></div>
    <div class="contact">
      <h1 class="contact__name">Daniel Brooks</h1>
      <p class="contact__role">Founder</p>
      <p class="contact__address">480 Harbor View Rd.<br>Lakeside Point, FL 33012</p>
      <ul class="contact__list">
        <li>
          <svg viewBox="0 0 10 10"><path d="M2 1 L3.6 1 L4.2 3 L3.2 3.8 Q4 5.8 6.2 6.8 L7 5.8 L9 6.4 L9 8 Q8.5 9 7.5 9 Q2 8 1 2.5 Q1 1.5 2 1Z" fill="var(--accent-sky)"/></svg>
          555-014-2290
        </li>
        <li>
          <svg viewBox="0 0 10 10"><rect x="0.8" y="2" width="8.4" height="6" fill="none" stroke="var(--accent-sky)" stroke-width="1.2"/><path d="M1 2.5 L5 5.5 L9 2.5" fill="none" stroke="var(--accent-sky)" stroke-width="1.2"/></svg>
          hello@brightpathhorizon.com
        </li>
        <li>
          <svg viewBox="0 0 10 10"><circle cx="5" cy="5" r="4" fill="none" stroke="var(--accent-sky)" stroke-width="1"/><ellipse cx="5" cy="5" rx="1.8" ry="4" fill="none" stroke="var(--accent-sky)" stroke-width="0.8"/><path d="M1 5 H9" stroke="var(--accent-sky)" stroke-width="0.8"/></svg>
          www.BrightpathHorizon.com
        </li>
      </ul>
    </div>
    <svg class="front-bands" viewBox="0 0 666 32" preserveAspectRatio="none">
      <rect x="0" y="18" width="346" height="14" fill="var(--brand-orange)"/>
      <polygon points="368,0 666,0 666,32 334,32" fill="var(--brand-navy)"/>
    </svg>
  </section>

  <section class="card card--back" aria-label="Business card back">
    <div class="brand-lockup">
      <span class="brand-lockup__dot"></span>
      <span class="brand-lockup__name">Brightpath Horizon</span>
    </div>
    <p class="back-web">www.yourwebsite.com</p>
  </section>
</main>
</body>
</html>
```